5 website banners (slides show)

We need 5 website sliding banners created for a website all about internet safety. The topics for each banner are:

Cyberbullying
Fraud
seniors
social networking

Sizes: 953 pixels x 281 pixels

I have stock images to use or feel free to use your own or one I can purchase from pixelharbor.example.

Industry/Entity Type

Internet

```html
<!DOCTYPE html>
<html lang="en">
<head>
<meta charset="utf-8">
<title>Fraud – Internet Safety Banner</title>
<link rel="stylesheet" href="https://fonts.googleapis.com/css2?family=Open+Sans:wght@300;400&display=swap">
<style>
  :root {
    --panel: #3e4651;
    --title: #f4f5f6;
    --body: #cfd3d8;
    --photo-warm: #d9d0c4;
    --photo-light: #e4e1dc;
    --photo-mid: #b9b8b6;
  }
  html, body {
    margin: 0;
    padding: 0;
    width: 1200px;
    height: 354px;
    overflow: hidden;
    background: var(--panel);
  }
  .banner {
    position: relative;
    width: 1200px;
    height: 354px;
    overflow: hidden;
    background: var(--panel);
    font-family: "Open Sans", Arial, sans-serif;
  }
  .banner__photo {
    position: absolute;
    left: 0;
    top: 0;
    width: 600px;
    height: 354px;
    background:
      linear-gradient(180deg, rgba(255,255,255,0.08) 0%, rgba(0,0,0,0.06) 100%),
      linear-gradient(90deg,
        var(--photo-warm) 0%,
        var(--photo-light) 35%,
        var(--photo-mid) 62%,
        #6f7680 82%,
        var(--panel) 97%);
  }
  .banner__content {
    position: absolute;
    right: 76px;
    top: 100px;
    width: 560px;
    text-align: right;
  }
  .banner__title {
    margin: 0;
    font-weight: 300;
    font-size: 60px;
    line-height: 1;
    color: var(--title);
    letter-spacing: -0.5px;
  }
  .banner__text {
    margin: 12px 0 0;
    font-weight: 400;
    font-size: 16.4px;
    line-height: 28px;
    color: var(--body);
  }
</style>
</head>
<body>
  <section class="banner">
    <div class="banner__photo" role="img" aria-label="Photo of an older woman at a desk holding a bank card while typing on a computer keyboard"></div>
    <div class="banner__content">
      <h1 class="banner__title">Fraud</h1>
      <p class="banner__text">Aliquam erat volutpat. Aliquam cursus sapien quis eros scelerisque,<br>sit amet interdum ligula ultrices non nulla sodales.</p>
    </div>
  </section>
</body>
</html>
```